Book cover

I am working with my publisher to publish my book They came up with a book cover but I don't like it. I want to see different designs. The book Title is Brightwater the subtitle Ways to Guide Teams Through Storms with Poise, Purpose & Pace by Marlene T. Ostrowski
I want to use my Brand Colors including the blue. I am uploading the covers of my other book. This is a professional leadership book. The publisher will make the cover when providing them a new design. the Brightwater one is one I played with on Canva. I would like more color and to incorporate the blue. I want a spot at the top where I can write a quote. Brightwater is one word in the text so should be the same on the cover. I want the cover to show energy movement and am open to an image too. I am attaching logos for the feel of the brand and brand rgb codes.

```html
<!DOCTYPE html>
<html lang="en">
<head>
<meta charset="utf-8">
<title>Brightwater — Book Cover</title>
<link rel="stylesheet" href="https://fonts.googleapis.com/css2?family=Bebas+Neue&family=Montserrat:wght@400;500;700&family=Roboto+Slab:wght@800&display=swap">
<style>
  :root {
    --cover-red: #ee1c1f;
    --title-red: #e8403c;
    --title-white: #f4f2ec;
    --author-teal: #1e8a8c;
    --paper: #efeee9;
    --ink-navy: #1b1a33;
    --amber: #f2a646;
    --teal-edge: #1f6b72;
  }
  * { margin: 0; padding: 0; box-sizing: border-box; }
  html, body { width: 980px; height: 1200px; overflow: hidden; background: var(--paper); }
  .cover { position: relative; width: 980px; height: 1200px; overflow: hidden; background: var(--paper); }

  .cover-photo {
    position: absolute; left: 0; top: 0; width: 980px; height: 1020px;
    background:
      radial-gradient(ellipse 55% 40% at 78% 18%, rgba(255,214,140,0.95), rgba(242,166,70,0) 70%),
      radial-gradient(ellipse 45% 35% at 30% 30%, rgba(200,120,60,0.7), rgba(200,120,60,0) 70%),
      linear-gradient(90deg, rgba(31,107,114,0.85) 0%, rgba(31,107,114,0) 12%, rgba(31,107,114,0) 88%, rgba(60,140,140,0.6) 100%),
      linear-gradient(180deg, #7a4a2c 0%, #a0622f 35%, #6a3b2a 55%, #3a2736 75%, var(--ink-navy) 100%);
  }

  .tagline {
    position: absolute; left: 83px; top: 122px;
    font-family: "Montserrat", sans-serif; font-weight: 700;
    font-size: 18px; line-height: 24px; letter-spacing: 0.2px;
    color: var(--title-white); text-transform: uppercase;
  }

  .title { position: absolute; left: 0; top: 270px; width: 980px; height: 210px; }
  .title text { font-family: "Bebas Neue", sans-serif; font-size: 240px; }
  .title .word-light { fill: var(--title-white); }
  .title .word-red { fill: var(--title-red); }

  .subtitle-band {
    position: absolute; left: 0; top: 611px; width: 980px; height: 131px;
    background: linear-gradient(90deg, var(--cover-red) 0%, #f0201c 60%, rgba(238,28,31,0.9) 100%);
    display: flex; flex-direction: column; align-items: center; justify-content: center;
    padding-left: 28px; color: #fff; font-family: "Montserrat", sans-serif; text-align: center;
  }
  .subtitle-lead { font-weight: 400; font-size: 27px; line-height: 36px; }
  .subtitle-values { font-weight: 500; font-size: 29px; line-height: 36px; letter-spacing: 0.6px; text-transform: uppercase; }

  .author-strip {
    position: absolute; left: 0; top: 1020px; width: 980px; height: 180px;
    background: var(--paper); display: flex; align-items: center; justify-content: center;
  }
  .author-name {
    font-family: "Roboto Slab", serif; font-weight: 800; font-size: 44px;
    letter-spacing: 0.5px; color: var(--author-teal); text-transform: uppercase;
  }
</style>
</head>
<body>
  <main class="cover">
    <div class="cover-photo" role="img" aria-label="Warm, sunlit, motion-blurred photo of people walking through a city street"></div>

    <p class="tagline">Brightwater is the essential playbook<br>to turn your uncertainty into possibility</p>

    <svg class="title" viewBox="0 0 980 210" aria-label="Brightwater">
      <text x="76" y="192" textLength="860" lengthAdjust="spacingAndGlyphs"><tspan class="word-light">BRIGHT</tspan><tspan class="word-red">WATER</tspan></text>
    </svg>

    <div class="subtitle-band">
      <p class="subtitle-lead">Ways to Guide Teams Through Storms with</p>
      <p class="subtitle-values">Poise, Purpose &amp; Pace</p>
    </div>

    <footer class="author-strip">
      <p class="author-name">Marlene T. Ostrowski</p>
    </footer>
  </main>
</body>
</html>
```